Maple Roster Business Card for recruitment company

We are looking for a Business Card Design that incorporates our personal details and our busines name and logo. We are a specialized search consultancy that recruit Property and Construction professionals.
We would like a business card that stands out and is appealing to the Construction and Property industry as well.

Target Market(s)

people in the construction and property industry

Contact Information for Business Card

Business Name and logo

Font styles to use
Serif

Colors
0094D4
00A9DD
6FCCEA
C7EBF8
E9F6FB

Requirements
Must have
• Business name and logo as well as contact details
Should not have
• No photos of us please

```html
<!DOCTYPE html>
<html lang="en">
<head>
<meta charset="utf-8">
<title>Maple Roster – Business Card</title>
<link rel="stylesheet" href="https://fonts.googleapis.com/css2?family=Questrial&family=Montserrat:wght@700&display=swap">
<style>
  :root {
    --stage: #e6e9ec;
    --card: #0d4258;
    --card-deep: #0a3549;
    --accent: #0094d4;
    --accent-bright: #00a9dd;
    --accent-soft: #6fccea;
    --ink: #ffffff;
    --ink-muted: #d7eef7;
  }
  * { box-sizing: border-box; margin: 0; padding: 0; }
  html, body {
    width: 1200px; height: 912px; overflow: hidden;
    background: var(--stage);
    font-family: "Questrial", sans-serif;
  }
  .canvas { position: relative; width: 1200px; height: 912px; }

  .card {
    position: absolute;
    width: 620px; height: 354px;
    background: var(--card);
    border-radius: 4px;
    overflow: hidden;
    box-shadow: 0 10px 28px rgba(10, 40, 55, 0.25);
  }
  .card-front { left: 60px; top: 60px; }
  .card-back { left: 520px; top: 498px; }

  .wordmark {
    position: absolute;
    display: flex; align-items: center; gap: 14px;
    color: var(--ink);
    font-family: "Questrial", sans-serif;
    letter-spacing: 0.12em;
    text-transform: uppercase;
    white-space: nowrap;
  }
  .wordmark-dot {
    width: 14px; height: 14px; border-radius: 50%;
    background: var(--accent-bright);
  }

  /* front */
  .front-decoration {
    position: absolute; inset: 0;
    background:
      radial-gradient(ellipse 70% 90% at 95% 10%, rgba(0,169,221,0.55), rgba(0,148,212,0.15) 55%, transparent 75%),
      linear-gradient(135deg, var(--card-deep) 0%, var(--card) 55%, #0f5877 100%);
  }
  .card-front .wordmark {
    left: 50%; top: 50%; transform: translate(-50%, -50%);
    font-size: 46px;
  }

  /* back */
  .back-decoration {
    position: absolute; right: 40px; top: 24px;
    width: 300px; height: 300px; border-radius: 50%;
    background: radial-gradient(circle at 60% 30%, rgba(0,169,221,0.45), rgba(0,148,212,0.12) 60%, transparent 72%);
  }
  .card-back .wordmark { left: 44px; top: 104px; font-size: 34px; }
  .edge-tab {
    position: absolute; left: -6px; top: 214px;
    width: 22px; height: 34px; border-radius: 6px;
    background: var(--ink);
  }
  .contact {
    position: absolute; left: 96px; top: 176px;
    color: var(--ink);
  }
  .contact-name {
    font-family: "Montserrat", sans-serif; font-weight: 700;
    font-size: 19px; letter-spacing: 0.05em; text-transform: uppercase;
  }
  .contact-role { font-size: 15px; color: var(--ink-muted); margin-bottom: 14px; }
  .contact-address { font-size: 14px; line-height: 1.4; margin-bottom: 12px; }
  .contact-lines { list-style: none; font-size: 14px; line-height: 1.5; }
  .contact-lines li { display: flex; align-items: center; gap: 8px; }
  .contact-lines svg { width: 12px; height: 12px; flex: none; }
</style>
</head>
<body>
<main class="canvas">
  <section class="card card-front" aria-label="Card front">
    <div class="front-decoration" role="img" aria-label="Repeating brand symbol pattern in blue tones"></div>
    <div class="wordmark"><span class="wordmark-dot"></span>Maple Roster</div>
  </section>

  <section class="card card-back" aria-label="Card back">
    <div class="back-decoration" role="img" aria-label="Large brand symbol"></div>
    <div class="edge-tab"></div>
    <div class="wordmark">Maple Roster</div>
    <div class="contact">
      <p class="contact-name">Owen Hartley</p>
      <p class="contact-role">Director</p>
      <p class="contact-address">118 Cedar Bend<br>Salem, OR 97301</p>
      <ul class="contact-lines">
        <li>
          <svg viewBox="0 0 12 12" fill="none" stroke="#fff" stroke-width="1.4" aria-hidden="true"><path d="M3 1.5 4.6 4 3.6 5.2a6 6 0 0 0 3.2 3.2L8 7.4l2.5 1.6-.8 1.6C5.5 10.6 1.4 6.5 1.4 2.3z"/></svg>
          (555) 214-3087
        </li>
        <li>
          <svg viewBox="0 0 12 12" fill="none" stroke="#fff" stroke-width="1.2" aria-hidden="true"><rect x="1" y="2.5" width="10" height="7" rx="1"/><path d="M1 3l5 3.5L11 3"/></svg>
          hello@mapleroster.com
        </li>
        <li>
          <svg viewBox="0 0 12 12" fill="none" stroke="#fff" stroke-width="1.1" aria-hidden="true"><circle cx="6" cy="6" r="5"/><ellipse cx="6" cy="6" rx="2.2" ry="5"/><path d="M1 6h10"/></svg>
          www.mapleroster.com
        </li>
      </ul>
    </div>
  </section>
</main>
</body>
</html>
```